Business card for Eyelash extension salon in Beverly Hills,California USA

We need new business card for our salon in Beverly Hills. The salon name is 'Lashvera' . We would like to have...Business name: Lashvera Name of person: will provide later Address 4720 N.Alder Crest Ave Beverly Hills , CA 90210 Phone: will provide later (Text only) Web: www.lashverastudio.example Snapgrid icon, Circlebook icon follow us for seasonal campaign and news @lashverastudiolounge Design should look elegant, high-end, clean, simple, cohesive with my brand. Please refer my brand board. Business name color will be metallic bronzy color. Im thinking grey background or white background. Thanks

Target Market(s)

25-35. Gender neutral. People who are in Entertainment business industry.
This is High-end Eyelash extension salon in Beverly Hills

Industry/Entity Type

Beauty Salon

Contact Information for Business Card

Business name: Lashvera
Name of person: will provide later
Address 4720 N.Alder Crest Ave Beverly Hills , CA 90210
Phone: will provide later (Text only)
Web: www.lashverastudio.example
Snapgrid icon, Circlebook icon
follow us for seasonal campaign and news @lashverastudiolounge

Requirements
Must have
• Beautiful, elegant, clean and simple look but very attractive and modern
Should not have
• We don't like too clutter, too busy designs.

```html
<!DOCTYPE html>
<html lang="en">
<head>
<meta charset="utf-8">
<title>Lashvera Business Card</title>
<link rel="stylesheet" href="https://fonts.googleapis.com/css2?family=Work+Sans:wght@300;400;500&family=Old+Standard+TT:wght@700&display=swap">
<style>
  :root {
    --backdrop: #2a2a2a;
    --card: #1c1c1c;
    --bronze: #8a6248;
    --bronze-line: #7d5a43;
    --ink: #ecebea;
    --rule-grey: #6d6d6d;
  }
  * { margin: 0; padding: 0; box-sizing: border-box; }
  html, body {
    width: 1093px;
    height: 1200px;
    overflow: hidden;
    background: var(--backdrop);
  }
  .canvas {
    position: relative;
    width: 1093px;
    height: 1200px;
  }
  .card {
    position: absolute;
    left: 191px;
    width: 711px;
    height: 411px;
    background: var(--card);
  }
  .card--front { top: 132px; }
  .card--back { top: 638px; }

  /* Front */
  .front-handle {
    position: absolute;
    left: 81px;
    top: 298px;
    font: 500 17px/1 "Work Sans", sans-serif;
    color: var(--bronze);
  }
  .brand {
    position: absolute;
    right: 78px;
    top: 218px;
    text-align: right;
  }
  .brand-name {
    display: block;
    font: 300 62px/1 "Work Sans", sans-serif;
    color: var(--bronze);
    letter-spacing: 1px;
  }
  .brand-place {
    display: block;
    margin-top: 14px;
    margin-right: 42px;
    font: 400 10.5px/1 "Work Sans", sans-serif;
    letter-spacing: 2.6px;
    color: var(--bronze);
  }

  /* Back */
  .person-name {
    position: absolute;
    left: 53px;
    top: 134px;
    font: 700 28px/1 "Old Standard TT", serif;
    letter-spacing: 1.5px;
    color: var(--bronze);
  }
  .rule {
    position: absolute;
    left: 52px;
    width: 445px;
    height: 1px;
  }
  .rule--top { top: 166px; background: var(--bronze-line); }
  .rule--mid { top: 275px; background: var(--bronze-line); }
  .rule--low { top: 323px; background: var(--rule-grey); }
  .contact-list {
    position: absolute;
    left: 52px;
    top: 185px;
    list-style: none;
    font: 300 17.5px/22.5px "Work Sans", sans-serif;
    color: var(--ink);
  }
  .social-handle {
    position: absolute;
    left: 56px;
    top: 286px;
    font: 300 17.5px/1.2 "Work Sans", sans-serif;
    color: var(--ink);
  }
  .address {
    position: absolute;
    left: 56px;
    top: 344px;
    font: 300 17.5px/1.2 "Work Sans", sans-serif;
    color: var(--ink);
  }
</style>
</head>
<body>
<main class="canvas">
  <section class="card card--front" aria-label="Card front">
    <p class="front-handle">@lashverastudiolounge</p>
    <div class="brand">
      <span class="brand-name">Lashvera</span>
      <span class="brand-place">BEVERLY HILLS</span>
    </div>
  </section>

  <section class="card card--back" aria-label="Card back">
    <h1 class="person-name">MARISOL DENBY</h1>
    <div class="rule rule--top"></div>
    <ul class="contact-list">
      <li>(310) 555 0148</li>
      <li>marisol@denbystudio.example</li>
      <li>www.lashverastudio.example</li>
    </ul>
    <div class="rule rule--mid"></div>
    <p class="social-handle">@lashverastudiolounge(snapgrid)</p>
    <div class="rule rule--low"></div>
    <p class="address">4720 N.Alder Crest Ave Beverly Hills , CA 90210</p>
  </section>
</main>
</body>
</html>
```